Coaching landingpage/salespage need a layout

Hi!
We are two people from Sweden looking for help to design our coaching landingpage/salespage.

What about:
We need a nice modern timeless appealing Photoshop layout (landingpage) for our coaching page where we coach people to “how to get a richer lifestyle”.

Style of page:
We want the site to reflect seriousness but still harmonic. We would like somewhat colorful and (but not too crazy). After all, we are coaching about investments and private economy.
Responsive layout – consider stacking order when scaling down window width. Fullpage-design where content areas are 960 grid/max-width.

----------------------------------------------------------------------------
Content on page:
*Headersection – Logo and header image with the two coaches together and space for later on adding a video.

*On the landingpage the customers can read up on what we mean by a richer lifestyle (use dummy text). We show our Vardagskompassen (= Lifestyle matrix) and a little description about that. If the customers want to know more, they can click "read more (or a symbolic icon that relates to read more)" to expand a hidden div (section) where they can read more about Vardagskompassen. They can also minimize the section.

*3-4 Unique selling points “Four reasons why choose coaching” with nice designed number-icons and some place for text.

*The customer should also be able to read something about what happens during a typical coaching session, some bullets that summarize it (use dummy text) and a couple of headlines, maybe 3 or 4 (about what they need to prepare for themselves .eg Talkwell, headset/microphone etc).

*Offer/product section: A section where the customer can see what services we provide, choose product and click order. When customer click order they will arrive to an order-page (this one you don’t have to design) .
Our products are as followed: Bronze (single coaching session), Silver (small-package), Gold (large-package). Use provided graphics for these products.

*Testimonials section. Currently we have 2 good testimonials, but only with text no portrait picture.

Testimonial1: “Uppiggande och inspirerande! Kommer med enkla vardagstips såväl som svårare tips. Ett roligt sätt att få en spark i baken, så att ekonomi-energin bibehålls! Tack för ett bra samtal!" - Helena Brattvik

Testimonial2: "Värdefullast för mig var kunskapen om alternativa investeringssställen som inte är börs eller eget ägande." - Annika Sjöstedt

*Section with portraits and info about the coaches (currently 2 coaches, but in future will be several, so a design-section that’s lets us add more coaches).

*Footer-section
------------------------------------------------------------------------

Colors:
Use Vardagskompassen (attached file) as colorinspiration. Doesn’t have to be exactly those colors, you can use similar colors if it is more pleasing to the eye and you can also use complementary colors.

Currently we have tried of our own but don't really nail it with any apealing design. This is what we have done so far but we want to replace it with your more professional design:

https://www.harborkite.se/full/Page/coaching13
-------------------------------------------------------------

SUMMARIZE of the above design-description:

* Our logo (attached psd-file with smart-object. You can try different colors with color-overlay)

*Apealing headerimage with portrait (attached file "big_portrait")

*Introduction text (use dummy text about 100 words)

*Text about Vardagskompassen (use dummy text about 200 words)

*Vardagskompassen (attached psd-file with smart-object)

*What we are covering during a coaching session (dummy text about 200 words and about 5 or 6 bullets)

*3-4 Unique Selling Points with stylish number icons (not 2 small) and some text.
*Our offers Bronze, Silver, Gold (attached pictures)
*Testimonials
*Picture & info about coaches (attached pictures, choose whichever suits you)
*Footer

Please comment if there are questions.

Target Market(s)

People who want to learn how to create a richer lifestyle which involves more freedom and a better well-being

Number of Pages Required

1 page

Font styles to use
Sans Serif
Other font styles liked:
• Roboto

Requirements
Should not have
• A cheezy unmodern landingpage with lots of texts and 10 sign-up buttons.
• This page is not a site about capturing emails and building lists by provide a "best-guide-for-something". It´s about getting people to book and pay for one or more coaching-sessions.

```html
<!DOCTYPE html>
<html lang="en">
<head>
<meta charset="utf-8">
<title>Harbor Kite – Step by step to a richer life</title>
<link href="https://fonts.googleapis.com/css2?family=Montserrat:wght@400;700&family=Lato:ital,wght@0,400;0,700;1,400&family=Roboto+Condensed:wght@400;700&display=swap" rel="stylesheet">
<style>
:root{
  --ink:#1e2a38;
  --text:#3b4450;
  --muted:#7a828c;
  --accent:#2e6a96;
  --band:#36658d;
  --button:#2f5f86;
  --soft:#eeeff1;
  --line:#d9dce0;
  --footer:#315876;
  --footer-deep:#27475f;
  --white:#ffffff;
}
*{box-sizing:border-box;margin:0;padding:0}
html,body{width:1200px;height:4110px;overflow:hidden}
body{font-family:'Lato',sans-serif;color:var(--text);background:var(--white);font-size:14px;line-height:1.55}
.section{position:relative;width:1200px}
.wrap{position:absolute;left:120px;width:960px}
.section-title{position:absolute;left:0;width:1200px;text-align:center;font-family:'Montserrat',sans-serif;font-weight:700;font-size:34px;color:var(--ink);letter-spacing:.5px}
.section-title span{color:var(--accent)}
.divider{position:absolute;left:500px;width:200px;height:14px}
.divider::before,.divider::after{content:"";position:absolute;top:10px;width:85px;height:1px;background:#9aa1a8}
.divider::before{left:0}.divider::after{right:0}
.divider i{position:absolute;left:93px;top:0;width:14px;height:12px;background:var(--ink)}
.btn{display:inline-block;background:var(--button);color:var(--white);font-family:'Roboto Condensed',sans-serif;text-align:center}

/* header + hero */
.hero{height:562px;background:linear-gradient(135deg,#f2f3f5 0%,#dfe2e6 40%,#eef0f2 65%,#d6d9de 100%)}
.brand{position:absolute;left:172px;top:18px;display:flex;align-items:center;gap:10px;font-family:'Lato',sans-serif;font-weight:700;font-size:24px;letter-spacing:2px;color:var(--accent)}
.brand b{display:block;width:22px;height:22px;background:var(--accent)}
.contact-bar{position:absolute;left:810px;top:22px;display:flex;align-items:center;gap:12px;font-size:22px;color:var(--ink)}
.social-square{position:absolute;left:995px;top:20px;width:32px;height:32px;background:var(--accent)}
.hero-title{position:absolute;left:172px;top:228px;font-family:'Roboto Condensed',sans-serif;font-weight:700;font-size:52px;line-height:1.1;color:var(--ink)}
.hero .btn{position:absolute;left:175px;top:378px;width:190px;height:52px;line-height:52px;font-size:26px;font-weight:700;border-radius:3px}
.video{position:absolute;left:562px;top:156px;width:465px;height:343px;background:#1d1f22;box-shadow:0 4px 14px rgba(0,0,0,.35)}
.video-scene{position:absolute;left:0;top:0;width:465px;height:296px;background:linear-gradient(180deg,#dfe3e6 0%,#c9cdd0 55%,#3a3f47 100%)}
.play{position:absolute;left:200px;top:118px;width:64px;height:64px;border-radius:50%;background:rgba(60,60,60,.7)}
.controls{position:absolute;left:0;top:296px;width:465px;height:47px;background:#18191b}

/* about */
.about{height:342px;background:var(--soft)}
.about p{position:absolute;left:186px;width:828px;top:143px;text-align:center;font-size:13.5px;line-height:1.55}
.about .btn{position:absolute;left:543px;top:254px;width:114px;height:36px;line-height:36px;font-size:15px;font-family:'Lato',sans-serif;font-weight:700;border-radius:2px}

/* lifestyle */
.lifestyle{height:740px;background:var(--white)}
.lifestyle h3{position:absolute;left:175px;top:156px;font-family:'Lato',sans-serif;font-weight:400;font-size:24px;color:var(--ink)}
.lifestyle .lead{position:absolute;left:175px;width:860px;top:198px;font-size:13.5px}
.matrix{position:absolute;left:164px;top:300px;width:360px;height:390px;border-radius:10px;background:linear-gradient(135deg,#eef4e6 0%,#f6f0dc 50%,#e9eef2 100%)}
.points{position:absolute;left:548px;top:310px;width:510px;list-style:none}
.points li{position:relative;padding-left:38px;margin-bottom:20px;font-size:13.2px;line-height:1.55}
.points svg{position:absolute;left:0;top:2px}

/* how */
.how{height:740px;background:var(--soft)}
.how .intro{position:absolute;left:175px;width:855px;top:88px;font-size:13.5px}
.how h4{position:absolute;left:175px;font-family:'Lato',sans-serif;font-weight:700;font-size:14px;color:var(--accent)}
.steps{position:absolute;left:175px;top:266px;width:803px;list-style:none;border-top:1px solid var(--line)}
.steps li{height:41px;line-height:41px;padding-left:10px;font-size:13.5px;color:var(--ink);border-bottom:1px solid var(--line);background:var(--white)}
.how .note{position:absolute;left:175px;width:855px;font-size:13.5px}

/* products */
.products{height:616px;background:var(--white)}
.card{position:absolute;top:159px;width:272px;height:402px;border:1px solid var(--line);background:var(--white);text-align:center}
.card .band{height:170px;background:var(--band);color:var(--white);font-family:'Roboto Condensed',sans-serif;font-weight:700;font-size:29px;padding-top:12px}
.coin{position:absolute;left:76px;top:70px;width:120px;height:120px;border-radius:50%}
.card .price{position:absolute;top:210px;width:100%;font-family:'Roboto Condensed',sans-serif;font-weight:700;font-size:40px;color:var(--ink)}
.card .includes{position:absolute;top:272px;width:100%;font-size:19px;color:var(--text)}
.card .btn{position:absolute;left:56px;top:327px;width:160px;height:44px;line-height:44px;font-size:24px}

/* testimonials */
.testimonials{height:384px;background:var(--soft)}
.quote{position:absolute;top:143px;height:145px;padding:22px 30px 0 70px;font-family:'Lato',sans-serif;font-style:italic;font-size:15px;line-height:1.65;color:var(--ink);background:var(--white)}
.quote::before{content:"\201C";position:absolute;left:20px;top:-6px;font-family:'Montserrat',sans-serif;font-size:70px;font-style:normal;color:#b8bdc3}
.quote cite{position:absolute;left:0;top:170px;width:100%;text-align:center;font-style:normal;font-size:14px;font-weight:700;color:var(--accent)}
.arrow{position:absolute;top:196px}

/* team */
.team{height:424px;background:var(--white)}
.member{position:absolute;top:156px;width:418px;height:227px;border:1px solid var(--line);box-shadow:0 2px 4px rgba(0,0,0,.08)}
.portrait{position:absolute;left:11px;top:11px;width:88px;height:93px;background:linear-gradient(180deg,#c7ccd2,#8e959e)}
.member h5{position:absolute;left:126px;top:60px;font-family:'Lato',sans-serif;font-weight:700;font-size:19px;color:var(--ink)}
.member .mail{position:absolute;left:126px;top:86px;font-size:12px;color:var(--muted)}
.member .bio{position:absolute;left:14px;top:118px;width:388px;font-style:italic;font-size:13.2px;line-height:1.6}
.member .bio span{color:var(--accent)}

/* footer */
.footer{height:274px;background:var(--footer);color:var(--white)}
.footer h6{position:absolute;top:30px;font-family:'Lato',sans-serif;font-weight:400;font-size:15px;letter-spacing:1.5px;color:#c9d6e2}
.links{position:absolute;left:175px;top:68px;list-style:none}
.links li{font-size:15px;height:36px;padding-left:14px;position:relative}
.links li::before{content:"›";position:absolute;left:0;color:#c9d6e2}
.footer .brand{position:absolute;left:175px;top:200px;font-size:19px;color:var(--white)}
.footer .brand b{width:16px;height:16px;background:var(--white)}
.address{position:absolute;left:433px;top:68px;font-size:14px;line-height:1.6}
.address .row{position:relative;padding-left:26px;margin-bottom:30px}
.address svg{position:absolute;left:0;top:3px}
.widget{position:absolute;left:753px;top:69px;width:272px;height:164px;background:var(--white);color:var(--ink);padding:10px}
.widget .head{display:flex;gap:8px;align-items:flex-start}
.widget .sq{width:40px;height:40px;background:var(--accent)}
.widget .name{font-weight:700;font-size:13px}
.widget .like{display:inline-block;margin-top:3px;width:34px;height:14px;background:#dde3ec;border:1px solid #b9c2cf}
.widget .count{font-size:11px;margin-top:8px}
.fans{display:flex;gap:6px;margin-top:6px}
.fans div{width:44px;text-align:center;font-size:10.5px}
.fans i{display:block;width:40px;height:40px;margin:0 auto 2px;background:linear-gradient(180deg,#c4cad1,#959ca5)}
.copyright{position:absolute;left:0;top:274px;width:1200px;height:28px;line-height:28px;text-align:center;font-size:12px;color:#c9d6e2;background:var(--footer-deep)}
</style>
</head>
<body>

<header class="section hero">
  <div class="brand"><b></b>HARBOR KITE</div>
  <div class="contact-bar">
    <svg width="28" height="28" viewBox="0 0 28 28"><circle cx="14" cy="14" r="14" fill="#1e2a38"/><path d="M10 8c1 0 2 2 2 3s-1 1.3-1 2c.5 1.6 2 3 3.6 3.6.7 0 1-1 2-1s3 1 3 2-1.3 2.4-3 2.4C12 20 8 16 8 11c0-1.7 1-3 2-3z" fill="#fff"/></svg>
    123-456-7890
  </div>
  <div class="social-square"></div>
  <h1 class="hero-title">STEP BY STEP<br>TO A RICHER LIFE</h1>
  <a class="btn">GET STARTED</a>
  <div class="video">
    <div class="video-scene" role="img" aria-label="Video still of the two coaches standing side by side in suits"></div>
    <svg class="play" viewBox="0 0 64 64"><path d="M25 19l21 13-21 13z" fill="#fff"/></svg>
    <svg class="controls" viewBox="0 0 465 47">
      <path d="M14 15l13 8.5-13 8.5z" fill="#fff"/>
      <path d="M42 19h5l6-5v19l-6-5h-5z" fill="#fff"/>
      <rect x="72" y="20" width="370" height="7" rx="3.5" fill="#3d4046"/>
      <rect x="72" y="20" width="130" height="7" rx="3.5" fill="#3f86c4"/>
    </svg>
  </div>
</header>

<section class="section about">
  <h2 class="section-title" style="top:43px">ABOUT <span>HARBOR KITE</span></h2>
  <div class="divider" style="top:95px"><i></i></div>
  <p>Lorem ipsum dolor sit amet, consectetur adipiscing elit. Vestibulum gravida ipsum nec tempor aliquam. Quisque sit amet est vel purus imperdiet ullamcorper lobortis id magna. Nulla in tellus risus. Morbi vitae tortor tincidunt velit aliquam sodales. Vivamus ex erat, pulvinar nec nunc vitae, maximus aliquet nunc. Aenean cursus dui at enim mattis, a blandit arcu volutpat. Donec leo turpis, viverra at justo ut, placerat ultricies nibh.</p>
  <a class="btn">Read More</a>
</section>

<section class="section lifestyle">
  <h2 class="section-title" style="top:44px">LIFESTYLE <span>MATRIX</span></h2>
  <div class="divider" style="top:96px"><i></i></div>
  <h3>What is a richer lifestyle?</h3>
  <p class="lead">What is a richer lifestyle may differ between different people. It can also be quite difficult on their own to get a good picture of what you really mean by this. We have therefore developed a simple model to facilitate the understanding and the creation of a richer lifestyle. This is a model we call lifestyle matrix and consists of the following four parts representing respective lifestyle.</p>
  <div class="matrix" role="img" aria-label="Vardagskompassen: a hand-drawn four-square matrix with the quadrants Välmående, En rikare livsstil, Ekorrhjulet and Frihet, with axes for well-being and freedom"></div>
  <ul class="points">
    <li><svg width="22" height="22" viewBox="0 0 22 22"><circle cx="11" cy="11" r="11" fill="#2e6a96"/><path d="M6 11h9M11 7l4 4-4 4" stroke="#fff" stroke-width="2" fill="none"/></svg>The matrix is a result of that we met more and more people begin to question the lifestyle they live today and look for other options.</li>
    <li><svg width="22" height="22" viewBox="0 0 22 22"><circle cx="11" cy="11" r="11" fill="#2e6a96"/><path d="M6 11h9M11 7l4 4-4 4" stroke="#fff" stroke-width="2" fill="none"/></svg>Options that often involves a combination of a highly prosperous and high freedom in life. This option we have chosen to define the matrix as a richer lifestyle.</li>
    <li><svg width="22" height="22" viewBox="0 0 22 22"><circle cx="11" cy="11" r="11" fill="#2e6a96"/><path d="M6 11h9M11 7l4 4-4 4" stroke="#fff" stroke-width="2" fill="none"/></svg>It is a lifestyle , where you , for example, does not need to sell one third of your time for money, especially not to a job you do not enjoy. Because we believe in that a richer lifestyle is not only a final destination , but also a way to travel.</li>
    <li><svg width="22" height="22" viewBox="0 0 22 22"><circle cx="11" cy="11" r="11" fill="#2e6a96"/><path d="M6 11h9M11 7l4 4-4 4" stroke="#fff" stroke-width="2" fill="none"/></svg>It's about feeling good and have fun along the way and not just at the end in the form of a short-lived lyckokick.</li>
    <li><svg width="22" height="22" viewBox="0 0 22 22"><circle cx="11" cy="11" r="11" fill="#2e6a96"/><path d="M6 11h9M11 7l4 4-4 4" stroke="#fff" stroke-width="2" fill="none"/></svg>I livsstilscoachingen använder vi Vardagskompassen som ett hjälpmedel för att kartlägga var du är just nu, vart du vill i framtiden och resvägen dit. På detta sätt fungerar kompassen som en form av övergripande karta.</li>
  </ul>
</section>

<section class="section how">
  <h2 class="section-title" style="top:74px;top:56px">HOW DOES <span>IT WORK?</span></h2>
  <div class="divider" style="top:108px"><i></i></div>
  <p class="intro" style="top:146px">Together with your coach you will develop a tailored approach that is appropriate for your circumstances and ambitions. This is because we humans are in different phases of life. Some need more time to find out what they really want to live the lifestyle while others have different obstacles in their path they need to address in order to achieve the results they want . There are many areas to focus on , depending on where you are in life.</p>
  <h4 style="top:240px">These are examples of different areas that your coach will go through with you:</h4>
  <ul class="steps">
    <li>Where Are You Right Now In Lifestyle Matrix ?</li>
    <li>Where Would You Be Lifestyle Matrix?</li>
    <li>Find A Route That Suits You And You Seem To Think Is Fun</li>
    <li>Getting Started , Or Build Your Own Money Machine</li>
    <li>Break Down Big Goals Into Manageable Sub-goals</li>
    <li>Continuously Check That You Are On Track And Making Progress</li>
  </ul>
  <h4 style="top:540px">What do I need ?</h4>
  <p class="note" style="top:565px">The call is implemented via the program Talkwell. All you need is a computer and a headset , alternatively, a microphone and speakers.</p>
  <h4 style="top:608px">How do I book coaching ?</h4>
  <p class="note" style="top:633px">Select a single session or one of our packages . Write what times of day that suits you best . We will contact you then to find a time that suits us both.</p>
</section>

<section class="section products">
  <h2 class="section-title" style="top:52px">OUR <span>PRODUCTS</span></h2>
  <div class="divider" style="top:104px"><i></i></div>
  <div class="card" style="left:175px">
    <div class="band">Engångsession</div>
    <div class="coin" role="img" aria-label="Bronze medal" style="background:radial-gradient(circle at 40% 35%,#f0b07a,#c46d2f 60%,#8e4a1c)"></div>
    <div class="price">Pris 650 SEK</div>
    <div class="includes">Inkluderar 1 session</div>
    <a class="btn">Boka Tid</a>
  </div>
  <div class="card" style="left:463px">
    <div class="band">Silverpaketet</div>
    <div class="coin" role="img" aria-label="Silver medal" style="background:radial-gradient(circle at 40% 35%,#ffffff,#c3c6ca 60%,#8d9196)"></div>
    <div class="price">Pris 3050 SEK</div>
    <div class="includes">Inkluderar 5 sessioner</div>
    <a class="btn">Boka Tid</a>
  </div>
  <div class="card" style="left:751px">
    <div class="band">Guldpaketet</div>
    <div class="coin" role="img" aria-label="Gold medal" style="background:radial-gradient(circle at 40% 35%,#fff3a6,#e9c12a 60%,#b18a0e)"></div>
    <div class="price">Pris 5800 SEK</div>
    <div class="includes">Inkluderar 10 sessioner</div>
    <a class="btn">Boka Tid</a>
  </div>
</section>

<section class="section testimonials">
  <h2 class="section-title" style="top:48px">CLIENTS <span>TESTIMONIALS</span></h2>
  <div class="divider" style="top:100px"><i></i></div>
  <svg class="arrow" style="left:118px" width="22" height="40" viewBox="0 0 22 40"><path d="M18 3L4 20l14 17" stroke="#8a9198" stroke-width="2.5" fill="none"/></svg>
  <blockquote class="quote" style="left:175px;width:415px">Uppiggande och inspirerande! Kommer med enkla vardagstips såväl som svårare tips. Ett roligt sätt att få en spark i baken, så att ekonomi-energin bibehålls! Tack för ett bra samtal!<cite>- Helena Brattvik</cite></blockquote>
  <blockquote class="quote" style="left:658px;width:383px">Värdefullast för mig var kunskapen om alternativa investeringsställen som inte är börs eller eget ägande.<cite>- Annika Sjöstedt</cite></blockquote>
  <svg class="arrow" style="left:1052px" width="22" height="40" viewBox="0 0 22 40"><path d="M4 3l14 17L4 37" stroke="#8a9198" stroke-width="2.5" fill="none"/></svg>
</section>

<section class="section team">
  <h2 class="section-title" style="top:40px">OUR <span>TEAM</span></h2>
  <div class="divider" style="top:92px"><i></i></div>
  <article class="member" style="left:175px">
    <div class="portrait" role="img" aria-label="Portrait of coach Joakim Hedlund"></div>
    <h5>Joakim Hedlund</h5>
    <div class="mail">joakim@harborkite.se</div>
    <p class="bio">Mångsidig investerare med fokus på alternativa och högriskinvesteringar. Förutom börsen, investerar Joakim i onoterade startup-bolag och olika internetbaserade investeringar såsom P2P-lending, onlinespel och appar.</p>
  </article>
  <article class="member" style="left:608px">
    <div class="portrait" role="img" aria-label="Portrait of coach Fredrik Lindqvist"></div>
    <h5>Fredrik Lindqvist</h5>
    <div class="mail">fredrik@harborkite.se</div>
    <p class="bio">Fredrik har en bred bakgrund inom ekonomi och IT. Som investerare ligger hans fokus på utdelningsaktier, fastigheter och internetbaserat entreprenörskap. Han har också en lång erfarenhet och en stor passion... <span>read more</span></p>
  </article>
</section>

<footer class="section footer">
  <h6 style="left:175px">QUICK LINKS</h6>
  <ul class="links"><li>Blogg</li><li>Coaching</li><li>Om oss</li></ul>
  <div class="brand"><b></b>HARBOR KITE</div>

  <h6 style="left:433px">CONTACT DETAILS</h6>
  <div class="address">
    <div class="row"><svg width="14" height="18" viewBox="0 0 14 18"><path d="M7 0C3 0 0 3 0 7c0 5 7 11 7 11s7-6 7-11c0-4-3-7-7-7z" fill="#fff"/><circle cx="7" cy="7" r="2.5" fill="#315876"/></svg><b>Harbor Kite</b><br>Harbor Kite AB, Kajgatan 12<br>411 05 Göteborg</div>
    <div class="row"><svg width="16" height="16" viewBox="0 0 16 16"><path d="M4 1c1 0 2 2.5 2 3.5S5 6 5 6.5c.6 1.8 2.4 3.5 4.5 4.3.6 0 1-1 2-1s3 1.2 3 2.2S13 15 11.5 15C6 15 1 10 1 4.5 1 2.5 2.6 1 4 1z" fill="#fff"/></svg>123-456-7890</div>
    <div class="row"><svg width="16" height="12" viewBox="0 0 16 12"><rect width="16" height="12" rx="1.5" fill="#fff"/><path d="M1 1l7 6 7-6" stroke="#315876" stroke-width="1.5" fill="none"/></svg>team@harborkite.se</div>
  </div>

  <h6 style="left:753px">FOLLOW ON FRIENDWALL</h6>
  <div class="widget">
    <div class="head"><div class="sq"></div><div><div class="name">Harbor Kite</div><span class="like"></span></div></div>
    <div class="count">4,575,158 people like Harbor Kite</div>
    <div class="fans">
      <div><i role="img" aria-label="Follower avatar"></i>John</div>
      <div><i role="img" aria-label="Follower avatar"></i>Nate</div>
      <div><i role="img" aria-label="Follower avatar"></i>Rita</div>
      <div><i role="img" aria-label="Follower avatar"></i>Wilson</div>
      <div><i role="img" aria-label="Follower avatar"></i>Sarah</div>
    </div>
  </div>
  <div class="copyright">Copyright © 2016 Harbor Kite. All Rights Reserved.</div>
</footer>

</body>
</html>
```